Executive Business Card for Healthcare Company [Need Today]

I need a business card design for a healthcare company. The only branding the company has thus far is a logo. The cards will be utilized by company executives. The design I envision will be vibrant and appealing but with a corporate feel. They shouldn't be too casual or playful. I would like to complete this project TODAY if possible.

Target Market(s)

Healthcare vendors, other executives in healthcare and pharmaceuticals

Industry/Entity Type

Pharmaceutical

Contact Information for Business Card

See attachment

Font styles to use
Serif
Sans Serif

Colors

Designer to choose colors to be used in the design.

```html
<!DOCTYPE html>
<html lang="en">
<head>
<meta charset="utf-8">
<title>Corvale Therapeutics – Executive Business Card</title>
<link rel="stylesheet" href="https://fonts.googleapis.com/css2?family=Questrial&display=swap">
<style>
  :root {
    --teal: #35bec5;
    --teal-text: #2fb8c0;
    --green-ring: #6cc69a;
    --ink: #4a4a4a;
    --divider: #7a7a7a;
    --paper: #ffffff;
    --ghost: #eef6f4;
    --backdrop: #1e1e1e;
  }
  * { margin: 0; padding: 0; box-sizing: border-box; }
  html, body {
    width: 1189px; height: 1200px; overflow: hidden;
    background: var(--backdrop);
    font-family: "Questrial", "Century Gothic", sans-serif;
  }
  .canvas { position: relative; width: 1189px; height: 1200px; }

  .card {
    position: absolute; left: 166px; width: 857px; height: 490px;
    overflow: hidden;
    box-shadow: 0 6px 18px rgba(0,0,0,.5);
  }

  /* Front */
  .card--front { top: 66px; background: var(--teal); }
  .card__pattern { position: absolute; inset: 0; background: var(--teal); }
  .front-brand {
    position: absolute; left: 50%; top: 50%;
    transform: translate(-50%, -50%);
    display: flex; align-items: center; gap: 22px;
    color: var(--paper);
  }
  .front-brand__circle {
    width: 114px; height: 114px; border-radius: 50%;
    border: 3px solid var(--paper);
  }
  .front-brand__name { font-size: 40px; line-height: 1; letter-spacing: .5px; }

  /* Back */
  .card--back { top: 625px; background: var(--paper); }
  .back-band {
    position: absolute; left: 0; top: 0; width: 106px; height: 100%;
    background: var(--teal);
    border-right: 3px solid var(--divider);
  }
  .ghost-circle {
    position: absolute; left: 450px; top: -21px;
    width: 408px; height: 408px; border-radius: 50%;
    border: 6px solid var(--ghost);
  }
  .back-brand__badge {
    position: absolute; left: 36px; top: 49px;
    width: 130px; height: 130px; border-radius: 50%;
    background: var(--paper);
  }
  .back-brand__badge::after {
    content: ""; position: absolute; inset: 8px; border-radius: 50%;
    border: 3px solid var(--green-ring);
  }
  .back-brand__name {
    position: absolute; left: 184px; top: 96px;
    font-size: 32px; line-height: 1; color: var(--teal-text);
  }

  .person { position: absolute; left: 184px; top: 292px; }
  .person__name { font-size: 25px; color: var(--teal-text); line-height: 1.1; }
  .person__title { font-size: 19px; color: var(--ink); line-height: 1.2; }

  .rule {
    position: absolute; left: 184px; top: 357px; width: 624px; height: 2px;
    background: var(--teal);
  }

  .contacts { position: absolute; left: 184px; top: 373px; list-style: none; }
  .contacts li {
    display: flex; align-items: center; gap: 6px;
    font-size: 20px; color: var(--ink); height: 27px;
  }
  .contacts svg { width: 20px; height: 20px; flex: none; }

  .address {
    position: absolute; left: 577px; top: 373px;
    font-size: 20px; color: var(--ink); font-style: normal;
  }
  .address span { display: block; height: 27px; line-height: 27px; }
  .address__company { color: var(--teal-text); }
</style>
</head>
<body>
<main class="canvas">

  <section class="card card--front" aria-label="Card front">
    <div class="card__pattern" role="img" aria-label="Subtle repeating pattern of the brand mark in tonal teal"></div>
    <div class="front-brand">
      <div class="front-brand__circle"></div>
      <span class="front-brand__name">Corvale Therapeutics</span>
    </div>
  </section>

  <section class="card card--back" aria-label="Card back">
    <div class="ghost-circle"></div>
    <div class="back-band"></div>
    <div class="back-brand__badge"></div>
    <span class="back-brand__name">Corvale Therapeutics</span>

    <div class="person">
      <p class="person__name">Daniel Marsh</p>
      <p class="person__title">Senior Director of Marketing</p>
    </div>

    <div class="rule"></div>

    <ul class="contacts">
      <li>
        <svg viewBox="0 0 20 20" aria-hidden="true"><circle cx="10" cy="10" r="8.5" fill="none" stroke="#6cc69a" stroke-width="1.5"/><rect x="7" y="5" width="6" height="10" rx="1" fill="none" stroke="#6cc69a" stroke-width="1.4"/></svg>
        555-214-7730
      </li>
      <li>
        <svg viewBox="0 0 20 20" aria-hidden="true"><circle cx="10" cy="10" r="9" fill="#6cc69a"/><path d="M5.5 8.5c0-2 9-2 9 0v1h-2.5v-1h-4v1H5.5z M7 10.5h6l1 3.5H6z" fill="#fff"/></svg>
        555-214-7815
      </li>
      <li>
        <svg viewBox="0 0 20 20" aria-hidden="true"><circle cx="10" cy="10" r="9" fill="#6cc69a"/><rect x="5" y="6.5" width="10" height="7" fill="#fff"/><path d="M5 6.5l5 4 5-4M5 13.5l5-4 5 4" fill="none" stroke="#6cc69a" stroke-width="1"/></svg>
        dmarsh@corvalerx.com
      </li>
    </ul>

    <address class="address">
      <span class="address__company">Corvale Therapeutics, LLC</span>
      <span>118 W Linden Avenue</span>
      <span>Fairview, GA 30599</span>
    </address>
  </section>

</main>
</body>
</html>
```